Velk Partners Building Business Cards

We need a business card that reflects our business as "Solar Experts" in San Diego. Browse our website www.velkpartners.example our License needs to be displayed as "CSLB# 3867140" our phone number is (619) 555-0187

Save thousands on your electric bills and increase the value of your home while helping to protect the environment. Our solar installation experts will help you design the system that's right for you, using only the highest quality equipment that will look great and give you ideal performance. Our goal is to make you energy independent, and get your electric bill to 0.

Paul Osterby
(619) 555-0187
paul@velkpartners.example

Target Market(s)

Home owners in san diego looking for solar

Industry/Entity Type

Solar Energy

Contact Information for Business Card

Paul Osterby
(619) 555-0187
paul@velkpartners.example

Font styles to use
Other font styles liked:
• Use our logo font

Requirements
Must have
• License needs to be displayed as "CSLB# 3867140" our phone number is (619) 555-0187
Nice to have
• Real images of rooftop home solar in san diego
Should not have
• our business address

```html
<!DOCTYPE html>
<html lang="en">
<head>
<meta charset="utf-8">
<title>Velk Partners Building – Business Card</title>
<link rel="stylesheet" href="https://fonts.googleapis.com/css2?family=Libre+Franklin:wght@400;600;800&display=swap">
<style>
  :root {
    --bg: #2b2b2b;
    --navy: #1b3f7a;
    --sun: #f7ae00;
    --sun-pale: #fde7ad;
    --white: #ffffff;
  }
  * { margin: 0; padding: 0; box-sizing: border-box; }
  html, body { width: 1200px; height: 987px; overflow: hidden; }
  body {
    background: var(--bg);
    font-family: "Libre Franklin", Arial, sans-serif;
    position: relative;
  }
  .card {
    position: absolute;
    left: 293px;
    width: 615px;
    height: 351px;
    overflow: hidden;
  }
  .card-front { top: 130px; background: var(--white); }
  .card-back { top: 505px; background: var(--sun); }

  .front-art { position: absolute; inset: 0; width: 100%; height: 100%; }

  .brand-name {
    font-weight: 800;
    color: var(--navy);
    white-space: nowrap;
    letter-spacing: -0.3px;
  }
  .card-front .brand-name {
    position: absolute;
    right: 29px;
    top: 86px;
    font-size: 21px;
  }

  .contact {
    position: absolute;
    left: 37px;
    top: 224px;
    color: var(--white);
    font-size: 14px;
    list-style: none;
  }
  .contact .license { margin-bottom: 14px; }
  .contact li { display: flex; align-items: center; height: 23.5px; }
  .contact svg { width: 13px; height: 13px; margin-right: 7px; fill: var(--sun); flex: none; }

  .person {
    position: absolute;
    right: 29px;
    top: 282px;
    text-align: right;
  }
  .person-name { color: var(--sun); font-size: 20px; font-weight: 600; line-height: 1.2; }
  .person-role { color: var(--white); font-size: 15px; line-height: 1.35; }

  .card-back .brand-name {
    position: absolute;
    left: 0; right: 0;
    top: 140px;
    text-align: center;
    font-size: 38px;
  }
  .card-back .web {
    position: absolute;
    left: 0; right: 0;
    top: 292px;
    text-align: center;
    color: var(--navy);
    font-size: 13px;
    letter-spacing: 5px;
  }
</style>
</head>
<body>

<section class="card card-front">
  <svg class="front-art" viewBox="0 0 525 300" preserveAspectRatio="none">
    <rect class="illustration-area" role="img" aria-label="Illustration area: rising sun over the hill"
          x="55" y="35" width="200" height="135" fill="var(--sun-pale)"/>
    <path class="wave-accent" fill="var(--sun)"
          d="M0,155 C40,138 70,126 100,125 C180,123 240,205 340,210 C430,213 490,175 525,140 L525,300 L0,300 Z"/>
    <path class="wave-band" fill="var(--navy)" stroke="var(--white)" stroke-width="1.6"
          d="M0,162 C40,145 70,133 100,132 C180,130 240,215 340,220 C430,223 490,187 526,150 L526,301 L-1,301 Z"/>
  </svg>

  <div class="brand-name">Velk Partners Building</div>

  <ul class="contact">
    <li class="license">CSLB# 3867140</li>
    <li><svg viewBox="0 0 16 16"><path d="M3 1h3l1.5 4-2 1.3a9 9 0 0 0 4.2 4.2L11 8.5l4 1.5v3a2 2 0 0 1-2 2A12 12 0 0 1 1 3a2 2 0 0 1 2-2z"/></svg>(619) 555-0187</li>
    <li><svg viewBox="0 0 16 16"><path d="M1 3h14v1.2L8 8.6 1 4.2z M1 6l7 4.4L15 6v7H1z"/></svg>paul@velkpartners.example</li>
    <li><svg viewBox="0 0 16 16"><circle cx="8" cy="8" r="7"/><path d="M1 8h14M8 1c-3 3-3 11 0 14M8 1c3 3 3 11 0 14" stroke="#1b3f7a" stroke-width="1.2" fill="none"/></svg>www.velkpartners.example</li>
  </ul>

  <div class="person">
    <div class="person-name">Paul Osterby</div>
    <div class="person-role">CEO/Founder</div>
  </div>
</section>

<section class="card card-back">
  <div class="brand-name">Velk Partners Building</div>
  <div class="web">www.velkpartners.example</div>
</section>

</body>
</html>
```